Business Card for Coach - ready to print

Design Business Card ready to order prints www.lukasbrenner.coach

* An Overview / Background of the Business & Services
· Coaching
· Personal growth
* The Target Market / Audience you are trying to reach
· private person in different roles (self, familiy, business role)s
* Design Specifics; any preferences or ideas for Style, Colour, Imagery, etc
· See www.lukasbrenner.coach
· "simple" design
· (small) element of surprise / unusual element

* Information that will be placed in the Business Card
· Beratung und Coaching
· Address: Lukas Brenner, Mosering 42, CH-8312 Winterthur, Mobile +41 79 264 53 07
* Do you have an existing website or Facebook page where designers can learn more about your company?
· lukasbrenner.coach

Target Market(s)

private person in different roles (self, familiy, business role)

Industry/Entity Type

Life Coaching

Contact Information for Business Card

Lukas Brenner
Mosering 42
CH-8312 Winterthur

Mobile: +41 79 264 53 07
Email: lubr@alpimail.ch
www.lukasbrenner.coach

Font styles to use
Sans Serif

Colors

Designer to choose colors to be used in the design.

Requirements
Must have
• "simple" design
• element of surprise / unusual element
• Beratung & Coaching
• see www.lukasbrenner.coach for colors and so...
Nice to have
• TA Symbol (three rings on top of each other) - unsual presentation
• QR Code of Website (see if it fits in and still looks good).

```html
<!DOCTYPE html>
<html lang="de">
<head>
<meta charset="utf-8">
<title>Lukas Brenner – Life Coaching Business Card</title>
<link rel="stylesheet" href="https://fonts.googleapis.com/css2?family=Oswald:wght@500&family=Montserrat:wght@500&family=Arimo:wght@400&display=swap">
<style>
  :root {
    --sky: #66cdf5;
    --slate: #575b62;
    --paper: #ffffff;
    --ink: #4a4d52;
    --backdrop: #e6e8eb;
    --photo-light: #b9bcc0;
    --photo-dark: #6f7378;
  }
  * { box-sizing: border-box; margin: 0; padding: 0; }
  html, body {
    width: 1200px; height: 880px; overflow: hidden;
    background: var(--backdrop);
  }
  .sheet {
    position: relative; width: 1200px; height: 880px;
    display: flex; flex-direction: column; align-items: center; justify-content: center; gap: 40px;
  }
  .card {
    position: relative; width: 600px; height: 388px;
    border-radius: 22px;
    box-shadow: 0 6px 22px rgba(0,0,0,.14);
    overflow: hidden;
  }
  /* front */
  .card-front { background: var(--sky); }
  .front-mark {
    position: absolute; left: 0; right: 0; top: 128px;
    text-align: center;
  }
  .wordmark {
    font-family: "Oswald", sans-serif; font-weight: 500;
    font-size: 78px; line-height: 1; letter-spacing: -1px;
    text-transform: uppercase;
  }
  .wordmark .first { color: var(--slate); }
  .wordmark .last { color: var(--paper); }
  .tagline {
    margin-top: 6px;
    font-family: "Montserrat", sans-serif; font-weight: 500;
    font-size: 20px; letter-spacing: 3px; color: var(--paper);
    padding-left: 40px;
  }
  /* back */
  .card-back { background: var(--paper); }
  .portrait {
    position: absolute; left: 76px; top: 92px;
    width: 204px; height: 204px; border-radius: 50%;
    border: 6px solid var(--sky);
    background: radial-gradient(circle at 50% 40%, var(--photo-light), var(--photo-dark));
  }
  .divider {
    position: absolute; left: 326px; top: 92px;
    width: 1.5px; height: 204px; background: var(--sky);
  }
  .contact {
    position: absolute; left: 352px; top: 96px;
    font-family: "Arimo", sans-serif; color: var(--ink);
    font-size: 15px; line-height: 1.4;
  }
  .contact .wordmark { font-size: 32px; letter-spacing: -.5px; margin-bottom: 14px; }
  .contact .wordmark .last { color: var(--sky); }
  .address { margin-left: 22px; margin-bottom: 4px; }
  .line { display: flex; align-items: center; gap: 8px; }
  .line svg { width: 14px; height: 14px; flex: none; }
  .accent { color: var(--sky); }
</style>
</head>
<body>
<main class="sheet">
  <section class="card card-front" aria-label="Card front">
    <div class="front-mark">
      <div class="wordmark"><span class="first">Lukas</span> <span class="last">Brenner</span></div>
      <div class="tagline">Life Coaching</div>
    </div>
  </section>

  <section class="card card-back" aria-label="Card back">
    <div class="portrait" role="img" aria-label="Portrait photo of Lukas Brenner"></div>
    <div class="divider"></div>
    <div class="contact">
      <div class="wordmark"><span class="first">Lukas</span> <span class="last">Brenner</span></div>
      <div class="address">Mosering 42<br>CH-8312 Winterthur</div>
      <div class="line">
        <svg viewBox="0 0 14 14" aria-hidden="true"><rect x="3" y="1" width="8" height="12" rx="1.5" fill="none" stroke="var(--sky)" stroke-width="1.4"/><circle cx="7" cy="11" r=".8" fill="var(--sky)"/></svg>
        <span>+41 79 264 53 07</span>
      </div>
      <div class="line">
        <svg viewBox="0 0 14 14" aria-hidden="true"><rect x="1" y="3" width="12" height="8" fill="var(--sky)"/><path d="M1 3 L7 8 L13 3" fill="none" stroke="#fff" stroke-width="1.2"/></svg>
        <span>lubr@alpimail.ch</span>
      </div>
      <div class="line">
        <svg viewBox="0 0 14 14" aria-hidden="true"><circle cx="7" cy="7" r="5.5" fill="none" stroke="var(--sky)" stroke-width="1.3"/><ellipse cx="7" cy="7" rx="2.4" ry="5.5" fill="none" stroke="var(--sky)" stroke-width="1.1"/><path d="M1.5 7 H12.5" stroke="var(--sky)" stroke-width="1.1"/></svg>
        <span>www.<span class="accent">lukasbrenner</span>.coach</span>
      </div>
    </div>
  </section>
</main>
</body>
</html>
```